Corbell Lending Partners - Real estate loans - need a business card with a logo

I need a logo and a business card that looks elegant - that looks as if it is a big stablish corporation - We do real estate loans, my goal is to brand myself with colors black background - gold or silver letters - some combination - Name of the company different color than the rest of the card -

```html
<!DOCTYPE html>
<html lang="en">
<head>
<meta charset="utf-8">
<title>Corbell Lending Partners – Business Card</title>
<link rel="stylesheet" href="https://fonts.googleapis.com/css2?family=Oswald:wght@500&family=Arimo:wght@400&display=swap">
<style>
  :root {
    --backdrop: #111111;
    --card: #1d1d1d;
    --card-edge: #262626;
    --silver: #c9c9c9;
    --silver-soft: #a9a9a9;
    --rule: #8a8a8a;
  }
  * { box-sizing: border-box; margin: 0; padding: 0; }
  html, body {
    width: 1200px; height: 900px; overflow: hidden;
    background: var(--backdrop);
  }
  .canvas {
    position: relative; width: 1200px; height: 900px;
    display: flex; flex-direction: column; align-items: center; justify-content: center;
    gap: 34px;
  }
  .card {
    width: 700px; height: 400px;
    background: linear-gradient(135deg, #1a1a1a 0%, var(--card) 55%, #252525 100%);
    border: 1px solid var(--card-edge);
    box-shadow: 0 14px 30px rgba(0,0,0,0.55);
    position: relative;
  }
  .card-front {
    display: flex; flex-direction: column; align-items: center; justify-content: center;
    gap: 22px;
  }
  .brand-square {
    width: 64px; height: 64px;
    border: 3px solid var(--silver);
  }
  .brand-name {
    font-family: "Arimo", sans-serif; font-weight: 400;
    font-size: 30px; letter-spacing: 4px; text-transform: uppercase;
    color: var(--silver);
  }
  .card-back {
    display: flex; align-items: center; justify-content: center;
  }
  .person {
    text-align: right; padding-right: 34px;
  }
  .person-name {
    font-family: "Oswald", sans-serif; font-weight: 500;
    font-size: 38px; letter-spacing: 2px; text-transform: uppercase;
    color: var(--silver); line-height: 1.1;
  }
  .person-role {
    font-family: "Arimo", sans-serif; font-size: 18px; color: var(--silver-soft);
    margin-top: 4px;
  }
  .divider {
    width: 2px; height: 140px; background: var(--rule);
  }
  .contact {
    padding-left: 34px;
    font-family: "Arimo", sans-serif; font-size: 18px; color: var(--silver);
    line-height: 1.4; list-style: none;
  }
  .contact li { display: flex; align-items: center; gap: 8px; }
  .contact svg { width: 14px; height: 14px; flex: none; }
</style>
</head>
<body>
<main class="canvas">
  <section class="card card-front">
    <div class="brand-square"></div>
    <div class="brand-name">Corbell Lending Partners</div>
  </section>

  <section class="card card-back">
    <div class="person">
      <div class="person-name">Daniel Rourke</div>
      <div class="person-role">Founder</div>
    </div>
    <div class="divider"></div>
    <ul class="contact">
      <li>418 Harlow Avenue</li>
      <li>Lindmere, WA 99240</li>
      <li>
        <svg viewBox="0 0 16 16" fill="none" stroke="#c9c9c9" stroke-width="1.6" stroke-linecap="round"><path d="M4 2l2.5 3-1.5 1.5c.8 1.8 2.2 3.2 4 4L10.5 9l3 2.5-1.5 2.5C7 13.5 2.5 9 2 4z"/></svg>
        555 310 4827
      </li>
      <li>
        <svg viewBox="0 0 16 16" fill="none" stroke="#c9c9c9" stroke-width="1.4"><rect x="1.5" y="3.5" width="13" height="9"/><path d="M1.5 3.5L8 9l6.5-5.5"/></svg>
        info@corbelllending.com
      </li>
      <li>
        <svg viewBox="0 0 16 16" fill="none" stroke="#c9c9c9" stroke-width="1.3"><circle cx="8" cy="8" r="6.5"/><ellipse cx="8" cy="8" rx="2.8" ry="6.5"/><path d="M1.5 8h13"/></svg>
        www.corbelllending.com
      </li>
    </ul>
  </section>
</main>
</body>
</html>
```